DESKHAVEN COSPACE Website design and coding

DESKHAVEN COSPACE

DESKHAVEN is Galveston’s first (and currently only) shared business co-working space. We share the same upscale, casual work environment, but we work independently on our own (or our team’s) projects and goals. For only a flat $195 membership fee per month, you have your very own all-inclusive, fun, personal business office environment. Website is written (Word file #12, below); and all pictures etc provided. Galveston is a beachy, coastal, historic city an hour from Houston, Texas USA. Logo (file 11 below) is temporary only.

Target Market(s)

Outside sales people, medical students looking for study hall, Houston companies looking for local office, real estate agents, graphic artists, entrepreneurs, etc

Contact Information for Business Card

will discuss --want to combine with current business card with multiple businesses

Logo Text

DESKHAVEN COSPACE

Coding

Coded - Design and coding required

Number of Pages Required

5+ page

Colors
ec1f27
fbed22

Requirements
Nice to have
• maroon/wine dominant with yellow and red accents, gray base are the colors of the space--website could coordinate--but open to creative ideas/combinations

```html
<!DOCTYPE html>
<html lang="en">
<head>
<meta charset="utf-8">
<title>DESKHAVEN COSPACE – Amenities</title>
<link href="https://fonts.googleapis.com/css2?family=Montserrat:wght@400;500;600;700;800&display=swap" rel="stylesheet">
<style>
  :root {
    --red: #cc0a1b;
    --yellow: #f9ea23;
    --ink: #111111;
    --logo-gray: #7a7a7a;
    --white: #ffffff;
  }
  * { margin: 0; padding: 0; box-sizing: border-box; }
  html, body { width: 917px; height: 1200px; overflow: hidden; background: var(--white); }
  body { font-family: "Montserrat", sans-serif; color: var(--ink); }
  .page { position: relative; width: 917px; height: 1200px; overflow: hidden; }

  .logo { position: absolute; font-weight: 800; font-size: 21px; letter-spacing: 0.5px; line-height: 1; }
  .site-header .logo { left: 103px; top: 17px; color: var(--logo-gray); }
  .nav { position: absolute; display: flex; gap: 0; font-size: 9.4px; font-weight: 500; letter-spacing: 0.1px; }
  .nav a { color: inherit; text-decoration: none; position: absolute; white-space: nowrap; }
  .site-header .nav { top: 20px; left: 0; color: var(--ink); }
  .nav a.active { color: var(--red); }

  .hero-photo { position: absolute; left: 0; top: 58px; width: 917px; height: 183px;
    background: linear-gradient(90deg, #8a8f94 0%, #5d5a55 20%, #9a9994 40%, #b7ab86 60%, #a47f54 80%, #6f5c4a 100%); }
  .intro { position: absolute; left: 104px; top: 195px; width: 485px; height: 88px; background: var(--yellow);
    border-left: 6px solid var(--red); padding: 16px 0 0 21px; }
  .intro h1 { font-size: 16px; font-weight: 700; line-height: 1.1; }
  .intro p { font-size: 12px; line-height: 1.35; font-weight: 400; }
  .intro .price { font-size: 16px; font-weight: 700; }

  .feature { position: absolute; background: var(--red); color: var(--white); font-size: 10.6px; font-weight: 500;
    line-height: 1.5; display: flex; align-items: center; padding: 0 6px 0 11px; border-radius: 2px; }
  .feature::before { content: ""; position: absolute; left: -14px; top: 50%; transform: translateY(-50%);
    width: 14px; height: 14px; background: var(--yellow); }
  .feature.tight { line-height: 1.15; }
  .col-left { left: 117px; width: 323px; }
  .col-right { left: 488px; width: 323px; padding-left: 9px; }

  .cta { position: absolute; left: 117px; top: 943px; width: 693px; height: 118px;
    background: linear-gradient(100deg, #7d7a4a 0%, #b7b35c 30%, #e9e0b6 48%, #c9c07d 65%, #a29c6a 100%); }
  .cta h2 { position: absolute; right: 18px; top: 22px; font-size: 21px; font-weight: 700; color: var(--ink); letter-spacing: 0.2px; }
  .cta .button { position: absolute; left: 541px; top: 59px; width: 129px; height: 33px; background: var(--red);
    color: var(--white); font-size: 9.4px; font-weight: 700; display: flex; align-items: center; justify-content: center; text-decoration: none; }

  .site-footer { position: absolute; left: 0; top: 1088px; width: 917px; height: 88px; background: var(--red); color: var(--white); }
  .site-footer .logo { left: 103px; top: 13px; color: var(--white); }
  .site-footer .nav { top: 23px; left: 0; color: var(--white); font-weight: 600; }
  .address { position: absolute; left: 104px; top: 43px; font-size: 9.4px; line-height: 1.22; font-weight: 500; }
  .copyright { position: absolute; left: 0; top: 1176px; width: 917px; height: 24px; background: var(--yellow);
    font-size: 8px; font-weight: 700; padding: 7px 0 0 104px; }
</style>
</head>
<body>
<div class="page">
  <header class="site-header">
    <div class="logo">DESKHAVEN</div>
    <nav class="nav">
      <a style="left:323px">ABOUT</a>
      <a class="active" style="left:373px">AMENITIES</a>
      <a style="left:445px">MEMBERSHIP</a>
      <a style="left:535px">PICTURES</a>
      <a style="left:605px">THE DESKHAVEN PILOSOPHY</a>
      <a style="left:762px">CONTACT</a>
    </nav>
  </header>

  <div class="hero-photo" role="img" aria-label="Photo of the shared kitchen with stone sink, steel refrigerator and a bar counter with stools"></div>
  <section class="intro">
    <h1>DESKHAVEN</h1>
    <p>is the first Galveston co-working space, and offers all of the following features, all included in your monthly <span class="price">$195</span> membership fee:</p>
  </section>

  <ul class="features">
    <li class="feature col-left" style="top:321px;height:35px">Open office or a private cubicle for your daily use.</li>
    <li class="feature col-left" style="top:366px;height:36px">Free Wifi.</li>
    <li class="feature col-left" style="top:409px;height:36px">24 hour access.</li>
    <li class="feature col-left tight" style="top:454px;height:35px;padding-left:8px">Comfortable open casual spaces or private office cubicles – at your option.</li>
    <li class="feature col-left" style="top:498px;height:35px">Communal coffee bar and kitchen, with FREE coffee.</li>
    <li class="feature col-left tight" style="top:541px;height:54px">Health and social distance amenities, including hand washing stations, and distanced desks with glass or wall separations, rigorous cleaning and sanitizing schedules.</li>
    <li class="feature col-left" style="top:603px;height:36px">Use of copier/printer (at per-copy cost).</li>
    <li class="feature col-left tight" style="top:645px;height:42px">Great modern design – a place that looks “cutting edge” and which you will be proud to call your own.</li>
    <li class="feature col-left" style="top:697px;height:41px">Keyless, digital door entry.</li>
    <li class="feature col-left" style="top:746px;height:42px">Mail service.</li>
    <li class="feature col-left" style="top:796px;height:35px;left:116px">Great opportunity for networking or mentoring.</li>
    <li class="feature col-left" style="top:841px;height:80px;left:116px">Building is a fabulous example of Mid-Century Modern architecture – lots of glass, open and light with luxurious granite floors and crisp Mid-Mod design. Private conference rooms for meetings.</li>

    <li class="feature col-right" style="top:321px;height:70px">Great location – a block from Galveston’s Post Office Street area of coffee bars, restaurants, bars, art galleries, and the Harborline Playhouse.</li>
    <li class="feature col-right" style="top:401px;height:71px">Weekly FREE happy hour with complimentary cocktails, beer and wine.  A great opportunity to make new friends and business contacts.</li>
    <li class="feature col-right" style="top:480px;height:71px">Free conference/presentation room, on a shared, scheduled basis.  Outfitted with modern flat screen for presentations.</li>
    <li class="feature col-right" style="top:560px;height:71px">Private lockable lockers – where you can permanently store your personal belongings, laptop, and work papers, safely and conveniently, and at no extra cost.</li>
    <li class="feature col-right" style="top:642px;height:74px">Very comfortable private office chairs, that fully adjust and recline, with an extendable foot rest; comfortable couches and communal spaces.</li>
    <li class="feature col-right" style="top:726px;height:120px">Kitchen and bar area, with commercial sink, refrigerator, dishwasher, microwave, hand-washing station, spacious prep counters – for everyone’s use! Bring your lunch; refrigerate (but name tag) your drinks!  All the comforts of home, without the hassles and distractions.</li>
    <li class="feature col-right" style="top:857px;height:63px">Very comfortable private office chairs, that fully adjust and recline, with an extendable foot rest; comfortable couches and communal spaces.</li>
  </ul>

  <section class="cta" role="img" aria-label="Photo of a potted plant in a round white vase on the kitchen counter">
    <h2>GET A FREE DAY, TO TRY US</h2>
    <a class="button">JOIN UR MEMBER</a>
  </section>

  <footer class="site-footer">
    <div class="logo">DESKHAVEN</div>
    <nav class="nav">
      <a style="left:324px">ABOUT</a>
      <a style="left:374px">AMENITIES</a>
      <a style="left:446px">MEMBERSHIP</a>
      <a style="left:536px">PICTURES</a>
      <a style="left:606px">THE DESKHAVEN PILOSOPHY</a>
      <a style="left:763px">CONTACT</a>
    </nav>
    <address class="address" style="font-style:normal">DESKHAVEN Cospace<br>418 Harbor Row, Suite 204<br>Galveston, TX 77554</address>
  </footer>
  <div class="copyright">Copyright 2020 DESKHAVEN COSPACE</div>
</div>
</body>
</html>
```